Professional Photography Business cards

I need business cards that include my logo which I have uploaded. I run a photography business. I am open to ideas but I would like one side to have my logo and the other side to have my contact info. I don't have a website made but I do own a website domain. I have uploaded 2 different logo color schemes. My business colors are Blue, black , and white.

Business Name
Business Phone Number
Business Email
Business Website address
Instagram

Industry/Entity Type

Professional Photography

Contact Information for Business Card

Phone Number: 916-384-7702 email: info@tlane-studio.example Instagram: @t.lanestudio website doman- www.tlane-studio.example

Requirements
Must have
• I like the idea of a business card with a full black background front and back of card. My colors must include royal blue, black, and white

```html
<!DOCTYPE html>
<html lang="en">
<head>
<meta charset="utf-8">
<title>T. Lane Photography — Business Card</title>
<link rel="stylesheet" href="https://fonts.googleapis.com/css2?family=Montserrat:wght@400;500;700&display=swap">
<style>
  :root {
    --backdrop: #d3d7d8;
    --card-white: #f4f4f2;
    --card-black: #060606;
    --royal-blue: #1f1f86;
    --ink: #1c1c1c;
    --silver: #9a9a9a;
  }
  * { box-sizing: border-box; margin: 0; padding: 0; }
  html, body {
    width: 1200px; height: 1049px; overflow: hidden;
    background: var(--backdrop);
    font-family: "Montserrat", sans-serif;
  }
  .sheet {
    width: 1200px; height: 1049px;
    display: flex; flex-direction: column; align-items: center; justify-content: center;
    gap: 48px;
  }
  .card {
    width: 760px; height: 434px;
    position: relative;
    box-shadow: 0 10px 30px rgba(0,0,0,0.18);
  }
  .card--contact { background: var(--card-white); }
  .card--brand {
    background: var(--card-black);
    display: flex; align-items: center; justify-content: center;
  }
  .brand {
    display: flex; align-items: center; gap: 14px;
  }
  .brand__mark {
    border-radius: 50%;
    border: 3px solid currentColor;
    flex: none;
  }
  .brand__name { font-weight: 500; white-space: nowrap; }
  .card--contact .brand {
    position: absolute; left: 44px; top: 190px;
    color: var(--royal-blue);
  }
  .card--contact .brand__mark { width: 40px; height: 40px; }
  .card--contact .brand__name { font-size: 25px; }
  .card--brand .brand { color: var(--silver); }
  .card--brand .brand__mark { width: 64px; height: 64px; }
  .card--brand .brand__name { font-size: 44px; }
  .divider {
    position: absolute; left: 378px; top: 110px;
    width: 2px; height: 214px;
    background: var(--royal-blue);
  }
  .details {
    position: absolute; left: 404px; top: 118px;
  }
  .details__name {
    color: var(--royal-blue); font-weight: 700; font-size: 30px; line-height: 1.1;
  }
  .details__title {
    color: var(--ink); font-weight: 500; font-size: 20px; margin-top: 6px;
  }
  .contact-list { list-style: none; margin-top: 24px; }
  .contact-list li {
    display: flex; align-items: center; gap: 10px;
    font-size: 17px; color: var(--ink); line-height: 1.75;
  }
  .contact-list svg { width: 18px; height: 18px; flex: none; }
</style>
</head>
<body>
<main class="sheet">
  <section class="card card--contact">
    <div class="brand">
      <span class="brand__mark"></span>
      <span class="brand__name">T. Lane Photography</span>
    </div>
    <div class="divider"></div>
    <div class="details">
      <h1 class="details__name">Tobias Lane</h1>
      <p class="details__title">CPA, CGA</p>
      <ul class="contact-list">
        <li>
          <svg viewBox="0 0 18 18" aria-hidden="true"><rect width="18" height="18" rx="2" fill="var(--royal-blue)"/><path d="M5 4c1 0 1.6 2 1.6 2.6 0 .6-1 1-1 1.6.5 1.5 2 3 3.4 3.5.6 0 1-1 1.6-1 .6 0 2.6.6 2.6 1.6 0 1-1.2 1.7-2 1.7C7.5 14 4 10.5 3.9 6 3.9 5 4.3 4 5 4z" fill="#fff"/></svg>
          916-384-7702
        </li>
        <li>
          <svg viewBox="0 0 18 18" aria-hidden="true"><rect width="18" height="18" rx="2" fill="var(--royal-blue)"/><rect x="3" y="5" width="12" height="8" fill="none" stroke="#fff" stroke-width="1.3"/><path d="M3 5l6 5 6-5" fill="none" stroke="#fff" stroke-width="1.3"/></svg>
          info@tlane-studio.example
        </li>
        <li>
          <svg viewBox="0 0 18 18" aria-hidden="true"><circle cx="9" cy="9" r="8" fill="var(--royal-blue)"/><ellipse cx="9" cy="9" rx="3.2" ry="6.5" fill="none" stroke="#fff" stroke-width="1.1"/><path d="M2.5 9h13" stroke="#fff" stroke-width="1.1"/></svg>
          www.tlane-studio.example
        </li>
        <li>
          <svg viewBox="0 0 18 18" aria-hidden="true"><rect width="18" height="18" rx="2" fill="var(--royal-blue)"/></svg>
          @t.lanestudio
        </li>
      </ul>
    </div>
  </section>

  <section class="card card--brand">
    <div class="brand">
      <span class="brand__mark"></span>
      <span class="brand__name">T. Lane Photography</span>
    </div>
  </section>
</main>
</body>
</html>
```